Landingpage design

We need a landingpage for a Chatterloom add campaign. We sell socks made of bamboo in super quality. Our customers loves us, and we have a 5 heart rating at scorevane.com.

We want to create a add campaign targeted new customers, and the offer is that they can buy 1 pair of bamboo socks as a test, for only 20 DKK (2,7 Euro) including shipment. Our webpage is www.tuvelo.dk, landingpage should be built i Kyvio, a wysiwyg editor. based on their template. like:
https://tuvelo.pemlorsite.com/13844-sales-page
https://tuvelo.pemlorsite.com/13696-sales-page
https://tuvelo.pemlorsite.com/13845-sales-page

You don't have to follow the templates 100% if you have better ideas. We have an account for snapvaultly, so please get stockphotos from here.

Bamboo socks has a lot of great selling points, you can see a good desciption here:
https://feltrano.com/us/why-bamboo

We expect you to have experience in landingpage design, and expect to end up with 2 landingpages we can splittest on.

This is the first of a number of landingpages we need in the future, so for the right person there will be plenty of more work.

Target Market(s)

Denmark

Industry/Entity Type

E-Commerce

Number of Pages Required

2 page

Colors

Designer to choose colors to be used in the design.

Requirements
Must have
• A great selling page, showing all the great things with bamboo socks. It should be supplied with good packshots from snapvaultly.com

```html
<!DOCTYPE html>
<html lang="en">
<head>
<meta charset="utf-8">
<title>Tuvelo – Bamboo Socks</title>
<link href="https://fonts.googleapis.com/css2?family=Roboto:wght@400;500;700&display=swap" rel="stylesheet">
<style>
:root{
  --sky-top:#7dd9ee;
  --sky-bottom:#5ea1ea;
  --ink:#4a4a4a;
  --muted:#7b7b7b;
  --green:#3bb083;
  --star:#f5b90a;
  --card:#f1f1f1;
  --offer-bg:#ececec;
  --footer:#1e2130;
  --white:#ffffff;
}
*{box-sizing:border-box;margin:0;padding:0}
html,body{width:1200px;height:2757px;overflow:hidden}
body{font-family:'Roboto',sans-serif;color:var(--ink);background:var(--white);position:relative}
section,footer{position:absolute;left:0;width:1200px}
.abs{position:absolute}
.center{text-align:center;left:0;width:1200px}
.section-title{font-size:35px;font-weight:400}
.underline{position:absolute;width:130px;height:1px;left:535px}

/* facts */
.facts{top:0;height:555px;background:linear-gradient(180deg,var(--sky-top),var(--sky-bottom));color:var(--white)}
.facts .section-title{top:95px}
.facts .underline{top:139px;background:rgba(255,255,255,.8)}
.facts .lead{top:158px;font-size:15.5px;line-height:25px;font-weight:500}
.fact{position:absolute;top:274px;width:300px;text-align:center}
.fact .icon{width:88px;height:88px;border-radius:50%;background:var(--white);margin:0 auto;display:flex;align-items:center;justify-content:center}
.fact p{margin-top:28px;font-size:15px;line-height:26px}

/* video */
.video{top:555px;height:724px;background:linear-gradient(135deg,#f4f4f4,#ececec)}
.video .section-title{top:95px}
.video .underline{top:141px;background:var(--ink)}
.video .lead{top:158px;font-size:15px;line-height:26px;color:var(--muted);font-weight:500}
.leaf{position:absolute;background:radial-gradient(ellipse at center,#6f8f45 0%,#7d9a52 45%,rgba(125,154,82,0) 72%)}
.player{left:292px;top:277px;width:614px;height:340px;border-radius:6px;background:linear-gradient(135deg,#7a4a2c,#5b3a26 45%,#2f5a55 70%,#8a6a46)}
.play{position:absolute;left:274px;top:137px;width:66px;height:66px;border-radius:50%;background:var(--green);display:flex;align-items:center;justify-content:center}

/* reviews */
.reviews{top:1279px;height:792px}
.reviews .stars{top:100px}
.reviews .section-title{top:146px;color:var(--ink)}
.reviews .underline{top:190px;background:var(--ink)}
.reviews .lead{top:210px;font-size:15px;line-height:27px;color:var(--muted);font-weight:500}
.review{position:absolute;top:325px;width:298px;height:272px;background:var(--card);text-align:center}
.review .who{position:absolute;top:42px;left:76px;display:flex;align-items:center;gap:12px}
.avatar{width:42px;height:42px;border-radius:50%;background:linear-gradient(135deg,#3a78b5,#c88a4a)}
.name{font-size:15px;text-align:left}
.review p{position:absolute;top:108px;left:24px;width:250px;font-size:14px;line-height:21px;color:var(--muted)}
.arrow{position:absolute;top:446px}
.btn{position:absolute;background:var(--green);color:var(--white);font-size:13px;font-weight:500;letter-spacing:.3px;display:flex;align-items:center;justify-content:center}
.reviews .btn{left:485px;top:651px;width:228px;height:35px}

/* offer */
.offer{top:2071px;height:439px;background:var(--offer-bg)}
.offer h2{position:absolute;left:134px;top:68px;font-size:41px;line-height:53px;font-weight:500;color:#555}
.benefits{position:absolute;left:134px;top:196px;list-style:none}
.benefits li{display:flex;align-items:center;gap:14px;font-size:15.5px;color:var(--muted);height:27.5px}
.offer .btn{left:134px;top:298px;width:193px;height:35px}
.offer .note{position:absolute;left:134px;top:342px;font-size:12px;color:var(--muted)}
.model{position:absolute;left:684px;top:6px;width:516px;height:433px;background:linear-gradient(160deg,#f1e9e4,#e8a39a 55%,#c99a6a)}

/* footer */
footer{top:2510px;height:247px;background:var(--footer);color:var(--white)}
.col{position:absolute;top:60px;width:300px}
.col h3{font-size:18px;font-weight:500;margin-bottom:14px}
.col p{font-size:12px;line-height:18px;color:#e4e4e8}
.col a{color:var(--green);text-decoration:none}
.social{display:flex;align-items:center;gap:8px;margin-top:12px;font-size:12px}
.social span.dot{width:20px;height:20px;border-radius:50%;background:var(--white)}
</style>
</head>
<body>

<section class="facts">
  <h2 class="abs center section-title">A Few Facts About Tuvelo</h2>
  <span class="underline"></span>
  <p class="abs center lead">We have been working on textile for more than 10 years. This ensures that all products<br>meet our high quality standards.</p>

  <div class="fact" style="left:134px">
    <div class="icon"><svg width="34" height="30" viewBox="0 0 34 30"><path d="M11 2 L2 7 L5 14 L9 12 L9 28 L25 28 L25 12 L29 14 L32 7 L23 2 C21 5 13 5 11 2Z" fill="#5ec3ea"/></svg></div>
    <p>Our mission is to give our<br>customers access to quality products<br>at a reasonable price.</p>
  </div>
  <div class="fact" style="left:450px">
    <div class="icon"><svg width="34" height="36" viewBox="0 0 34 36"><rect x="7" y="4" width="5" height="28" fill="#5ec3ea"/><rect x="20" y="4" width="5" height="28" fill="#5ec3ea"/><path d="M12 14 C18 10 22 8 28 9 C24 13 20 15 12 16Z" fill="#5ec3ea"/><path d="M25 22 C29 20 31 22 32 25 C28 26 26 25 25 22Z" fill="#5ec3ea"/></svg></div>
    <p>We know that the properties of bamboo<br>are absolutely amazing and can reduce,<br>for example, sweaty and sour toes.</p>
  </div>
  <div class="fact" style="left:766px">
    <div class="icon"><svg width="30" height="36" viewBox="0 0 30 36"><circle cx="15" cy="13" r="11" fill="#5ec3ea"/><circle cx="15" cy="13" r="5" fill="#fff"/><path d="M8 22 L5 34 L11 31 L14 35 L15 24Z M22 22 L25 34 L19 31 L16 35 L15 24Z" fill="#5ec3ea"/></svg></div>
    <p>We shop directly with the<br>factories. This ensures the highest<br>quality at a competitive price.</p>
  </div>
</section>

<section class="video">
  <div class="leaf" role="img" aria-label="Green leaves decoration" style="left:-40px;top:-10px;width:310px;height:230px"></div>
  <div class="leaf" role="img" aria-label="Green leaves decoration" style="left:1020px;top:420px;width:220px;height:310px"></div>
  <h2 class="abs center section-title">A Short Video About Our Work</h2>
  <span class="underline"></span>
  <p class="abs center lead">We sell stockings, t-shirts, sweaters and men's boxershorts. If you choose our<br>subscription service, the products will come to you automatically.</p>
  <div class="abs player" role="img" aria-label="Video still: packed suitcase with shoes, shirt and travel items on a wooden floor">
    <div class="play"><svg width="24" height="28" viewBox="0 0 24 28"><path d="M3 2 L22 14 L3 26Z" fill="#fff"/></svg></div>
  </div>
</section>

<section class="reviews">
  <div class="abs center stars"><svg width="160" height="30" viewBox="0 0 160 30"><g fill="var(--star)"><path id="st" d="M15 1 L19 11 L29 11 L21 17 L24 28 L15 21 L6 28 L9 17 L1 11 L11 11Z"/><use href="#st" x="32"/><use href="#st" x="64"/><use href="#st" x="96"/><use href="#st" x="128"/></g></svg></div>
  <h2 class="abs center section-title">We Have a 5 Stars Rating</h2>
  <span class="underline"></span>
  <p class="abs center lead">You're in a good company. Here are some important facts and<br>testimonials about us.</p>

  <svg class="arrow" style="left:102px" width="16" height="24" viewBox="0 0 16 24"><path d="M12 3 L4 12 L12 21" stroke="var(--green)" stroke-width="3" fill="none"/></svg>
  <svg class="arrow" style="left:1080px" width="16" height="24" viewBox="0 0 16 24"><path d="M4 3 L12 12 L4 21" stroke="var(--green)" stroke-width="3" fill="none"/></svg>

  <div class="review" style="left:134px">
    <div class="who"><div class="avatar" role="img" aria-label="Reviewer portrait"></div><div><div class="name">Ren Calloway</div><svg width="90" height="16" viewBox="0 0 160 30"><g fill="var(--star)"><use href="#st"/><use href="#st" x="32"/><use href="#st" x="64"/><use href="#st" x="96"/><use href="#st" x="128"/></g></svg></div></div>
    <p>Lorem ipsum dolor sit amet, consetetur sadipscing elitr, sed diam nonumy eirmod tempor invidunt ut labore et dolore magna aliquyam erat, sed diam voluptua. At vero eos et accusam et justo duo</p>
  </div>
  <div class="review" style="left:450px">
    <div class="who"><div class="avatar" role="img" aria-label="Reviewer portrait"></div><div><div class="name">Ren Calloway</div><svg width="90" height="16" viewBox="0 0 160 30"><g fill="var(--star)"><use href="#st"/><use href="#st" x="32"/><use href="#st" x="64"/><use href="#st" x="96"/><use href="#st" x="128"/></g></svg></div></div>
    <p>Lorem ipsum dolor sit amet, consetetur sadipscing elitr, sed diam nonumy eirmod tempor invidunt ut labore et dolore magna aliquyam erat, sed diam voluptua. At vero eos et accusam et justo duo</p>
  </div>
  <div class="review" style="left:766px">
    <div class="who"><div class="avatar" role="img" aria-label="Reviewer portrait"></div><div><div class="name">Ren Calloway</div><svg width="90" height="16" viewBox="0 0 160 30"><g fill="var(--star)"><use href="#st"/><use href="#st" x="32"/><use href="#st" x="64"/><use href="#st" x="96"/><use href="#st" x="128"/></g></svg></div></div>
    <p>Lorem ipsum dolor sit amet, consetetur sadipscing elitr, sed diam nonumy eirmod tempor invidunt ut labore et dolore magna aliquyam erat, sed diam voluptua. At vero eos et accusam et justo duo</p>
  </div>

  <div class="btn">MORE REVIEWS</div>
</section>

<section class="offer">
  <div class="model" role="img" aria-label="Smiling woman in a pink sweater and white knit hat holding a paper shopping bag"></div>
  <h2>Get Your First Pair of Bamboo<br>Socks for Only 20 DKK</h2>
  <ul class="benefits">
    <li><svg width="16" height="12" viewBox="0 0 16 12"><path d="M1 6 L6 11 L15 1" stroke="var(--green)" stroke-width="2" fill="none"/></svg>Powerfully insulating - keeps you cooler in summer and warmer in winter</li>
    <li><svg width="16" height="12" viewBox="0 0 16 12"><path d="M1 6 L6 11 L15 1" stroke="var(--green)" stroke-width="2" fill="none"/></svg>Antibacterial - keeps you odor free and feeling and smelling fresh</li>
    <li><svg width="16" height="12" viewBox="0 0 16 12"><path d="M1 6 L6 11 L15 1" stroke="var(--green)" stroke-width="2" fill="none"/></svg>Most eco-friendly fabric on the planet - help save your planet</li>
  </ul>
  <div class="btn">BUY NOW</div>
  <p class="note">Shipment Included</p>
</section>

<footer>
  <div class="col" style="left:134px">
    <h3>About us</h3>
    <p>At Tuvelo.dk we specialize in basic products in<br>bamboo. We sell stockings, t-shirts, sweaters and<br>men's boxershorts</p>
    <div class="social"><span class="dot"></span>Chatterloom</div>
  </div>
  <div class="col" style="left:450px">
    <h3>Contact us</h3>
    <p>Any questions? Then e-mail <a href="mailto:info@tuvelo.dk">info@tuvelo.dk</a><br>or call us at +45 31 47 26 90</p>
    <p style="margin-top:8px">Or send us a letter to Tuvelo<br>Lindvej 14<br>7100 Vejle</p>
  </div>
  <div class="col" style="left:766px">
    <h3>Navigation</h3>
    <p>Home &nbsp;|&nbsp; Why Bamboo &nbsp;|&nbsp; About &nbsp;|&nbsp; Reviews</p>
  </div>
</footer>

</body>
</html>
```